Re designing of website of VELTRIS Pens, an International stationary brand

We would like to re design our existing website veltrispens.com. We are leading manufacturers and exporters of stationary products. Our existence is global -selling and marketing in all 5 continents.

We are a 35year old group with focus on high quality, innovative designs and state of art manufacturing setup.

Client satisfaction by committed service and trust are the roots of our organisation.

We would like to see a website which focuses on our brand Veltris and must have an international appeal. Our target buyers would be Agents, distributors and wholesalers in various countries. Content would be similar to our existing website but designing and outlook needs to be totally different.

For the outlook we do like the following websites from our industry which can be used to draw inspiration.
1. www.duniverastationery.com
2. www.quorlapen.com
3. www.haltmivopen.com

The homepage need not be focused on the product but must emphasis on the branding of Veltris, our existence of 35years along with international presence and quality standards maintained by our organisation.
Updates

Reason: Would like to see some more concepts and designs as per artwork attached.

Target Market(s)

Wholesalers, Agents and Distributors in all countries around the world. Target market is global

Number of Pages Required

1 page

Font styles to use
Sans Serif

Requirements
Must have
• Focus on Branding, High Quality Standards, Customer Loyalty
Nice to have
• Like the outlook of the websites
• www.haltmivopen.com
• www.duniverastationery.com
• www.quorlapen.com
Should not have
• Don't like the outlook of our present website www.veltrispens.com
• It doesn't justify our brand or our product

```html
<!DOCTYPE html>
<html lang="en">
<head>
<meta charset="utf-8">
<title>VELTRIS Pens</title>
<link rel="stylesheet" href="https://fonts.googleapis.com/css2?family=Open+Sans:wght@400;600&family=Oswald:wght@400&display=swap">
<style>
:root{
  --red:#d0202a;
  --red-dark:#b01b24;
  --panel:#a8191f;
  --white:#ffffff;
  --ink:#333333;
  --muted:#7a7a7a;
  --accent:#d9533a;
  --footer:#1f1f1f;
  --footer-line:#333333;
  --field:#ececec;
}
*{box-sizing:border-box;margin:0;padding:0}
html,body{width:1084px;height:1200px;overflow:hidden;background:var(--white);font-family:"Open Sans",sans-serif;color:var(--ink)}
.page{position:relative;width:1084px;height:1200px}
.abs{position:absolute}

.topbar{left:0;top:0;width:1084px;height:52px;background:var(--red);color:var(--white);font-size:12px}
.topbar .item{position:absolute;top:17px;display:flex;align-items:center;gap:6px;white-space:nowrap}
.topbar .right{font-size:10.5px;font-weight:600;top:18px}
.topbar .divider{position:absolute;left:151px;top:13px;width:2px;height:22px;background:var(--white)}

.logo{left:91px;top:76px;width:260px;height:63px;background:var(--red);display:flex;align-items:center;gap:12px;padding-left:10px}
.logo .mark{width:44px;height:44px;background:var(--white)}
.logo .name{font-size:40px;font-weight:600;color:var(--white);letter-spacing:1px;line-height:1}

.search{left:678px;top:85px;width:224px;height:25px;background:var(--field);font-size:10px;color:#999;padding:6px 10px}
.search-btn{left:903px;top:85px;width:34px;height:25px;background:var(--red);display:flex;align-items:center;justify-content:center}
.currency{left:678px;top:114px;font-size:11px;color:#bbb;display:flex;gap:7px}
.currency .on{color:var(--accent);font-weight:600}
.flag{left:771px;top:117px;width:16px;height:11px}
.cart-box{left:947px;top:85px;width:47px;height:41px;background:#f0f0f0;border-radius:3px;display:flex;align-items:center;justify-content:center}

.hero{left:0;top:161px;width:1084px;height:537px;background:radial-gradient(ellipse at 75% 40%,#e9c6bc 0%,#c99a8f 45%,#8f6259 100%)}
.hero-arrow{top:418px;width:32px;height:32px;border-radius:50%;background:rgba(255,255,255,.55);display:flex;align-items:center;justify-content:center}
.caption{left:278px;top:612px;width:556px;height:44px;background:rgba(240,232,230,.92);font-size:19px;font-weight:600;color:#3a3a3a;display:flex;align-items:center;justify-content:center;white-space:nowrap}

.categories{left:91px;top:161px;width:251px;height:388px;background:var(--panel);color:var(--white)}
.categories .head{height:51px;background:var(--red);font-size:20px;display:flex;align-items:center;justify-content:center;gap:16px;letter-spacing:.5px}
.categories .group{position:absolute;left:27px;right:20px;font-size:14px;font-weight:600;display:flex;justify-content:space-between;align-items:center;line-height:18px}
.categories ul{position:absolute;left:27px;top:92px;list-style:none;font-size:12px}
.categories li{height:26.4px;display:flex;align-items:center;gap:16px}
.categories li::before{content:"";width:6px;height:6px;border-radius:50%;background:var(--white)}

.mainnav{left:342px;top:161px;width:653px;height:51px;background:var(--white);display:flex;align-items:center;justify-content:flex-end;gap:34px;padding-right:12px;font-size:11.5px;font-weight:600;color:#555}

.deals-title{left:88px;top:742px;font-family:"Oswald",sans-serif;font-weight:400;font-size:23px;color:#444;line-height:1.2}
.deals-sub{left:88px;top:781px;font-size:13.5px;color:#333}
.deals-copy{left:88px;top:804px;width:179px;font-size:10.5px;line-height:16.2px;color:var(--muted);text-align:justify}
.read-more{left:159px;top:948px;width:106px;height:24px;background:var(--red);color:var(--white);font-size:12.5px;display:flex;align-items:center;justify-content:center}
.pager{top:747px;width:20px;height:20px;border:1px solid #ddd;display:flex;align-items:center;justify-content:center}
.view-all{left:948px;top:754px;font-size:12px;color:#444}

.card{top:786px;width:204px}
.card .photo{width:204px;height:184px;position:relative}
.card .ribbon{position:absolute;left:10px;top:-3px;width:28px;height:52px;background:#e2575e;clip-path:polygon(0 0,100% 0,100% 100%,50% 84%,0 100%)}
.card .ribbon span{position:absolute;left:50%;top:22px;transform:translate(-50%,-50%) rotate(-90deg);color:var(--white);font-size:11px;font-weight:600;white-space:nowrap;line-height:1}
.card .ribbon small{font-size:6px}
.card .overlay{position:absolute;left:0;top:72px;width:204px;height:58px;background:rgba(0,0,0,.45);color:var(--white);font-size:15px;text-align:center;padding-top:5px}
.card .overlay .btn{position:absolute;left:66px;top:32px;width:76px;height:26px;background:var(--red);font-size:15px;display:flex;align-items:center;justify-content:center}
.card h3{margin-top:12px;text-align:center;font-size:15px;font-weight:400;color:var(--accent)}
.card p{margin-top:6px;text-align:center;font-size:11px;line-height:16px;color:#444;padding:0 4px}

.footer{left:0;top:1122px;width:1084px;height:78px;background:var(--footer);color:var(--white)}
.footer-nav{position:absolute;left:0;width:1084px;top:13px;display:flex;justify-content:center;gap:9px;font-size:10.5px}
.footer-nav .sep{color:#ccc}
.footer-line{position:absolute;left:0;top:42px;width:1084px;height:1px;background:var(--footer-line)}
.copyright{position:absolute;left:90px;top:52px;font-size:10px}
.social{position:absolute;top:52px;width:15px;height:15px;border-radius:50%;background:var(--white)}
</style>
</head>
<body>
<div class="page">

  <header class="topbar abs">
    <div class="item" style="left:90px">
      <svg width="14" height="14" viewBox="0 0 14 14"><circle cx="7" cy="4" r="3.2" fill="#fff"/><path d="M1 14c0-4 2.5-6 6-6s6 2 6 6z" fill="#fff"/></svg>Login</div>
    <div class="divider"></div>
    <div class="item" style="left:164px">
      <svg width="10" height="13" viewBox="0 0 10 13"><rect x="0" y="5" width="10" height="8" fill="#fff"/><path d="M2.5 5V3.5a2.5 2.5 0 0 1 5 0V5" stroke="#fff" stroke-width="1.5" fill="none"/></svg>Create an Account</div>
    <div class="item right" style="left:653px">
      <svg width="11" height="10" viewBox="0 0 11 10"><path d="M5.5 10L1 5.5A2.6 2.6 0 0 1 5.5 1.8 2.6 2.6 0 0 1 10 5.5z" fill="#8d1118"/></svg>Wish List (0)</div>
    <div class="item right" style="left:746px">
      <svg width="11" height="11" viewBox="0 0 14 14"><circle cx="7" cy="4" r="3.2" fill="#fff"/><path d="M1 14c0-4 2.5-6 6-6s6 2 6 6z" fill="#fff"/></svg>My Account</div>
    <div class="item right" style="left:832px">
      <svg width="12" height="11" viewBox="0 0 12 11"><path d="M0 4h12l-1.5 7h-9z" fill="#fff"/><path d="M3 4l2-3M9 4L7 1" stroke="#fff" stroke-width="1.2"/></svg>Shopping Cart</div>
    <div class="item right" style="left:931px">
      <svg width="12" height="11" viewBox="0 0 12 11"><path d="M0 3.5h6V0l6 5.5-6 5.5V7.5H0z" fill="#fff"/></svg>Checkout</div>
  </header>

  <div class="logo abs"><div class="mark"></div><span class="name">VELTRIS</span></div>

  <div class="search abs">Search item here</div>
  <div class="search-btn abs">
    <svg width="11" height="11" viewBox="0 0 11 11"><circle cx="4.5" cy="4.5" r="3.5" stroke="#fff" stroke-width="1.6" fill="none"/><path d="M7 7l3 3" stroke="#fff" stroke-width="1.8"/></svg>
  </div>
  <div class="currency abs"><span class="on">$</span><span>|</span><span>€</span><span>|</span><span>£</span></div>
  <svg class="flag abs" viewBox="0 0 16 11">
    <rect width="16" height="11" fill="#c8323a"/>
    <rect y="1.6" width="16" height="1.6" fill="#fff"/><rect y="4.7" width="16" height="1.6" fill="#fff"/><rect y="7.8" width="16" height="1.6" fill="#fff"/>
    <rect width="7" height="6" fill="#2a3f8a"/>
  </svg>
  <div class="cart-box abs">
    <svg width="22" height="20" viewBox="0 0 22 20"><path d="M1 2h3l3 11h11l2-8H6" stroke="#777" stroke-width="1.6" fill="none"/><circle cx="8.5" cy="17" r="1.6" fill="#777"/><circle cx="16.5" cy="17" r="1.6" fill="#777"/></svg>
  </div>

  <section class="hero abs" role="img" aria-label="Close-up of a hand writing with a black ballpoint pen on paper"></section>
  <div class="hero-arrow abs" style="left:26px">
    <svg width="12" height="14" viewBox="0 0 12 14"><path d="M8 2L3 7l5 5" stroke="#999" stroke-width="2.2" fill="none"/></svg>
  </div>
  <div class="hero-arrow abs" style="left:1026px">
    <svg width="12" height="14" viewBox="0 0 12 14"><path d="M4 2l5 5-5 5" stroke="#999" stroke-width="2.2" fill="none"/></svg>
  </div>
  <div class="caption abs">35 years of quality writing, trusted on 5 continents.</div>

  <nav class="mainnav abs">
    <span>Home</span><span>Reatail Products</span><span>Promotional Products</span><span>Careers</span><span>Enquiry Form</span><span>Contact Us</span>
  </nav>

  <aside class="categories abs">
    <div class="head">Categories
      <svg width="12" height="10" viewBox="0 0 12 10"><path d="M0 0h12L6 10z" fill="#fff"/></svg>
    </div>
    <div class="group" style="top:66px">Retail Products
      <svg width="13" height="13" viewBox="0 0 13 13"><circle cx="6.5" cy="6.5" r="6.5" fill="#fff"/><rect x="3" y="5.6" width="7" height="1.8" fill="#a8191f"/></svg>
    </div>
    <ul>
      <li>Ball Pens</li><li>Gel Pens</li><li>Metal Pens</li><li>Art Material</li><li>Office Stationery</li><li>Notebooks</li><li>Refills</li><li>Packaging</li><li>POP</li>
    </ul>
    <div class="group" style="top:335px">Promotional Products
      <svg width="13" height="13" viewBox="0 0 13 13"><circle cx="6.5" cy="6.5" r="6.5" fill="#fff"/><rect x="3" y="5.6" width="7" height="1.8" fill="#a8191f"/><rect x="5.6" y="3" width="1.8" height="7" fill="#a8191f"/></svg>
    </div>
  </aside>

  <h2 class="deals-title abs">Hot Deal’s</h2>
  <div class="deals-sub abs">Hot Deal’s of the day :-</div>
  <p class="deals-copy abs">Veltris gives you the latest deal’s of the day. For 35 years our pens have met strict international quality standards, serving loyal agents and distributors in all five continents.</p>
  <div class="read-more abs">Read More</div>

  <div class="pager abs" style="left:302px">
    <svg width="8" height="8" viewBox="0 0 8 8"><path d="M5.5 1L2.5 4l3 3" stroke="#ccc" stroke-width="1.4" fill="none"/></svg>
  </div>
  <div class="pager abs" style="left:330px;border-color:#f0b8b8">
    <svg width="8" height="8" viewBox="0 0 8 8"><path d="M2.5 1l3 3-3 3" stroke="#e07a7a" stroke-width="1.4" fill="none"/></svg>
  </div>
  <div class="view-all abs">View All</div>

  <article class="card abs" style="left:302px">
    <div class="photo" role="img" aria-label="Black fountain pen on dark textured surface" style="background:linear-gradient(160deg,#1a1a1a 0%,#3a3a3a 55%,#8a8a8a 100%)">
      <div class="ribbon"><span>60%<small> OFF</small></span></div>
      <div class="overlay">Events<div class="btn">View</div></div>
    </div>
    <h3>Lorem Ipsum</h3>
    <p>random text. It has roots in a piece of classical Latin</p>
  </article>

  <article class="card abs" style="left:546px">
    <div class="photo" role="img" aria-label="Calculator, pen and keyboard on a white desk" style="background:linear-gradient(160deg,#e8e8e8 0%,#cfcfcf 55%,#9a9a9a 100%)">
      <div class="ribbon"><span>55%<small> OFF</small></span></div>
    </div>
    <h3>Lorem Ipsum</h3>
    <p>random text. It has roots in a piece of classical Latin</p>
  </article>

  <article class="card abs" style="left:791px">
    <div class="photo" role="img" aria-label="Quill, ink bottle and wax seal on a wooden table" style="background:linear-gradient(160deg,#3a2a1c 0%,#7a5a3a 55%,#a8804f 100%)">
      <div class="ribbon"><span>65%<small> OFF</small></span></div>
    </div>
    <h3>Lorem Ipsum</h3>
    <p>random text. It has roots in a piece of classical Latin</p>
  </article>

  <footer class="footer abs">
    <nav class="footer-nav">
      <span>Home</span><span class="sep">|</span><span>Categories</span><span class="sep">|</span><span>Create</span><span class="sep">|</span><span>Browse</span><span class="sep">|</span><span>Gallery</span><span class="sep">|</span><span>Contact</span>
    </nav>
    <div class="footer-line"></div>
    <div class="copyright">© 2015 Yoursite, All rights reserved.</div>
    <div class="social" style="left:929px"></div>
    <div class="social" style="left:954px"></div>
    <div class="social" style="left:979px"></div>
  </footer>

</div>
</body>
</html>
```